We are a local Communty Pharmacy wishing to promote and market a specialised Pharmaceutical Service

We would like a design that is professional and enticing ( according to the brief In attached files)
We wish to Market Compounding Pharmacy as a specialist side of our business.
We have the expertise a purpose built preparation laboratory.
The main purpose is an Internet presence that entices prospective patients to contact or visit our physical store.

Target Market(s)

Patients Medicos and Veterinary clients

Industry/Entity Type

Pharmacy

Coding

Coded - Design and coding required

Number of Pages Required

1 page

Requirements
Must have
• Clear friendly image
Nice to have
• soft enticing feel
Should not have
• No crass loud unprofessional elements

```html
<!DOCTYPE html>
<html lang="en">
<head>
<meta charset="utf-8">
<title>Compounding Pharmacy</title>
<link href="https://fonts.googleapis.com/css2?family=Open+Sans:wght@400;600;700&display=swap" rel="stylesheet">
<style>
:root{
  --page-blue:#1c5da6;
  --page-blue-dark:#154b8a;
  --nav-navy:#123d6e;
  --brand-blue:#1f62ad;
  --brand-green:#7cc242;
  --text-dark:#333a44;
  --text-muted:#8a9099;
  --white:#ffffff;
  --hero-tint:#eef2f5;
  --line:#e3e7eb;
}
*{box-sizing:border-box;margin:0;padding:0}
html,body{width:863px;height:1200px;overflow:hidden}
body{font-family:"Open Sans",Arial,sans-serif;background:var(--page-blue);color:var(--text-dark);position:relative}

.site-header{position:absolute;left:86px;top:0;width:691px;height:108px}
.brand{position:absolute;left:0;top:16px;display:flex;align-items:center;gap:10px}
.brand-mark{width:40px;height:40px;background:var(--white);border-radius:4px}
.brand-name{color:var(--white);font-size:19px;font-weight:600;line-height:1.15}
.contact-box{position:absolute;right:0;top:18px;text-align:right;color:var(--white)}
.contact-title{font-size:15px;font-weight:400}
.contact-line{font-size:8px;line-height:1.4;opacity:.9;margin-top:4px}
.social{display:flex;gap:5px;justify-content:flex-end;margin-top:7px}
.social span{width:16px;height:16px;border-radius:50%;background:#4a86c6}
.social span:nth-child(2){background:#e0483c}
.social span:nth-child(3){background:#5fb6e8}

.main-nav{position:absolute;left:86px;top:108px;width:691px;height:30px;background:var(--nav-navy);display:flex;align-items:center;padding-left:20px;gap:28px}
.main-nav a{color:var(--white);font-size:10px;text-decoration:none}

.page{position:absolute;left:86px;top:138px;width:691px;height:990px;background:var(--white)}

.hero{position:absolute;left:10px;top:8px;width:671px;height:356px;background:linear-gradient(90deg,#f4f6f8 0%,var(--hero-tint) 55%,#dfe8ef 100%);overflow:hidden}
.hero-photo{position:absolute;right:0;top:0;width:300px;height:356px;background:linear-gradient(160deg,#e6edf2 0%,#cfdbe4 60%,#bcccd8 100%)}
.hero-copy{position:absolute;left:34px;top:50px;width:360px}
.hero-title{color:var(--brand-blue);font-size:27px;font-weight:700;letter-spacing:.3px}
.hero-sub{color:var(--brand-green);font-size:15px;font-weight:600;margin-top:6px}
.hero-text{font-size:10px;line-height:1.6;color:var(--text-dark);margin-top:14px;width:320px}
.btn-outline{display:inline-block;margin-top:28px;border:1px solid var(--text-dark);border-radius:3px;padding:8px 12px;font-size:10px;color:var(--text-dark);background:var(--white)}
.slider-arrows{position:absolute;right:10px;bottom:12px;display:flex;gap:4px}
.slider-arrows span{width:16px;height:16px;background:#222;display:flex;align-items:center;justify-content:center}

.welcome{position:absolute;left:0;top:382px;width:691px;text-align:center}
.section-title{font-size:16px;font-weight:600;color:var(--text-dark);letter-spacing:.3px}
.section-lead{font-size:9px;color:var(--text-muted);margin-top:4px}
.features{display:flex;justify-content:space-between;padding:0 44px;margin-top:22px}
.feature{width:124px;text-align:center}
.feature-icon{width:70px;height:70px;border-radius:50%;background:var(--brand-blue);margin:0 auto;display:flex;align-items:center;justify-content:center}
.feature-icon.green{background:var(--brand-green)}
.feature-name{font-size:8.5px;font-weight:700;margin-top:14px;color:var(--text-dark)}
.feature-text{font-size:6.5px;line-height:1.5;color:var(--text-muted);margin-top:6px}

.about{position:absolute;left:0;top:580px;width:691px;height:400px;border-top:1px solid var(--line)}
.about-copy{position:absolute;left:20px;top:38px;width:380px}
.about-title{font-size:16px;font-weight:600}
.about-lead{font-size:10px;color:var(--text-muted);margin-top:6px}
.about-text{font-size:7px;line-height:1.7;color:var(--text-muted);margin-top:18px}
.btn-small{display:inline-block;margin-top:44px;border:1px solid #bbb;border-radius:2px;padding:4px 8px;font-size:7px;color:var(--text-dark)}
.about-photo{position:absolute;right:20px;top:26px;width:262px;height:190px;background:linear-gradient(135deg,#d9e4ec 0%,#b9cdd9 55%,#9fb7c7 100%)}

.site-footer{position:absolute;left:86px;top:1150px;width:691px;display:flex;justify-content:space-between;color:var(--white);font-size:8px}
</style>
</head>
<body>
<header class="site-header">
  <div class="brand">
    <span class="brand-mark"></span>
    <div class="brand-name">Compounding<br>Pharmacy</div>
  </div>
  <div class="contact-box">
    <div class="contact-title">Contact us Now !</div>
    <div class="contact-line">Call our lab team today for advice<br>and a friendly consultation now</div>
    <div class="social"><span></span><span></span><span></span><span></span></div>
  </div>
</header>

<nav class="main-nav">
  <a href="#">Home</a><a href="#">About us</a><a href="#">Locations</a><a href="#">Testings</a><a href="#">Contact</a>
</nav>

<main class="page">
  <section class="hero">
    <div class="hero-photo" role="img" aria-label="Smiling pharmacist in a white coat with a stethoscope"></div>
    <div class="hero-copy">
      <h1 class="hero-title">COMPOUNDING PHARMACY</h1>
      <p class="hero-sub">Ullamco laboris nisi ut aliquip commodo</p>
      <p class="hero-text">Lorem ipsum dolor sit amet, consectetur adipisicing elit, sed do eiusmod tempor incididunt ut labore et dolore magna aliqua. Ut enim ad minim veniam, quis nostrud exercitation ullamco laboris nisi ut aliquip ex ea commodo consequat. Duis aute irure dolor in reprehenderit in voluptate velit esse.</p>
      <span class="btn-outline">Get Free Consultation</span>
    </div>
    <div class="slider-arrows">
      <span><svg width="8" height="8" viewBox="0 0 8 8"><path d="M5 1 2 4l3 3" stroke="#fff" stroke-width="1.5" fill="none"/></svg></span>
      <span><svg width="8" height="8" viewBox="0 0 8 8"><path d="M3 1l3 3-3 3" stroke="#fff" stroke-width="1.5" fill="none"/></svg></span>
    </div>
  </section>

  <section class="welcome">
    <h2 class="section-title">WELCOME TO OUR COMPOUNDING PHARMACY</h2>
    <p class="section-lead">Lorem ipsum dolor sit amet, consectetur adipisicing elit, sed do eiusmod tempor incididunt ut labore</p>
    <div class="features">
      <div class="feature">
        <div class="feature-icon"><svg width="34" height="34" viewBox="0 0 34 34"><path d="M4 17 17 4h12v12L16 29z" fill="none" stroke="#fff" stroke-width="3" stroke-linejoin="round"/><circle cx="23" cy="10" r="2.5" fill="#fff"/></svg></div>
        <div class="feature-name">DINSECTETUR ADIPISICING</div>
        <p class="feature-text">Lorem ipsum dolor sit amet, consectetur adipisicing elit sed do eiusmod tempor incididunt</p>
      </div>
      <div class="feature">
        <div class="feature-icon green"><svg width="36" height="36" viewBox="0 0 36 36"><rect x="4" y="12" width="28" height="12" rx="6" transform="rotate(-35 18 18)" fill="#fff"/><line x1="18" y1="10" x2="18" y2="26" transform="rotate(-35 18 18)" stroke="#7cc242" stroke-width="2"/></svg></div>
        <div class="feature-name">EIUSMOD TEMPOR</div>
        <p class="feature-text">Lorem ipsum dolor sit amet, consectetur adipisicing elit sed do eiusmod tempor incididunt</p>
      </div>
      <div class="feature">
        <div class="feature-icon"><svg width="34" height="34" viewBox="0 0 34 34"><circle cx="17" cy="17" r="13" fill="none" stroke="#fff" stroke-width="3"/><path d="M17 8l4 9-4 9-4-9z" fill="#fff"/></svg></div>
        <div class="feature-name">ET DOLORE MAGNA</div>
        <p class="feature-text">Lorem ipsum dolor sit amet, consectetur adipisicing elit sed do eiusmod tempor incididunt</p>
      </div>
      <div class="feature">
        <div class="feature-icon"><svg width="32" height="32" viewBox="0 0 32 32"><path d="M11 2h10v9h9v10h-9v9H11v-9H2V11h9z" fill="#fff"/></svg></div>
        <div class="feature-name">NOSTRUD EXERCITATION</div>
        <p class="feature-text">Lorem ipsum dolor sit amet, consectetur adipisicing elit sed do eiusmod tempor incididunt</p>
      </div>
    </div>
  </section>

  <section class="about">
    <div class="about-copy">
      <h2 class="about-title">ABOUT COMPOUNDING PHARMACY</h2>
      <p class="about-lead">Lorem ipsum dolor sit amet, consectetur adipisicing elit, sed do eiusmod tempor</p>
      <p class="about-text">Sed ut perspiciatis unde omnis iste natus error sit voluptatem accusantium doloremque laudantium, totam rem aperiam, eaque ipsa quae ab illo inventore veritatis et quasi architecto beatae vitae dicta sunt explicabo. Nemo enim ipsam voluptatem quia voluptas sit aspernatur aut odit aut fugit, sed quia consequuntur magni dolores eos qui ratione voluptatem sequi nesciunt. Neque porro quisquam est, qui dolorem ipsum quia dolor sit amet.</p>
      <span class="btn-small">Read More</span>
    </div>
    <div class="about-photo" role="img" aria-label="Pharmacists at work in the compounding laboratory"></div>
  </section>
</main>

<footer class="site-footer">
  <span>Copyright © 2015 Compounding Pharmacy. Privacy policy</span>
  <span>Top</span>
</footer>
</body>
</html>
```